Coastline Premier Retreats Business Card Design

Design a business card for Coastline Premier Retreats. Look at the website for colors and reference. Card should have logo, name, title, office number, mobile number, email, URL and a tagline like, "Luxury Hotel & Resort Email Marketing" (This might change).

https://www.coastlinepremierretreats.example

The rest I will leave up to your imagination.

Contact Information for Business Card

Logo, name, title, office number, mobile number, email, URL and a tagline like, "Luxury Hotel & Resort Email Marketing" (This might change).

```html
<!DOCTYPE html>
<html lang="en">
<head>
<meta charset="utf-8">
<title>Coastline Premier Retreats – Business Card</title>
<link href="https://fonts.googleapis.com/css2?family=Poppins:wght@400;600;700;800&display=swap" rel="stylesheet">
<style>
  :root {
    --stage: #2b2b2b;
    --ink: #000000;
    --paper: #ffffff;
    --accent: #f57300;
    --rule: #8a8a8a;
  }
  * { box-sizing: border-box; margin: 0; padding: 0; }
  html, body { width: 1200px; height: 689px; overflow: hidden; }
  body {
    background: var(--stage);
    font-family: 'Poppins', sans-serif;
    position: relative;
  }
  .card {
    position: absolute;
    top: 190px;
    width: 540px;
    height: 309px;
    border-radius: 22px;
    overflow: hidden;
    box-shadow: 0 12px 30px rgba(0,0,0,.45);
  }
  /* Back side */
  .card-back { left: 40px; background: var(--ink); }
  .card-back .brand {
    position: absolute; top: 0; left: 0; right: 0; height: 222px;
    display: flex; align-items: center; justify-content: center; gap: 14px;
  }
  .brand-mark { width: 16px; height: 16px; background: var(--accent); flex: none; }
  .card-back .brand-name {
    color: var(--paper); font-weight: 800; font-size: 25px;
    letter-spacing: 1px; text-transform: uppercase; line-height: 1.1;
  }
  .tagline-band {
    position: absolute; left: 0; right: 0; bottom: 0; height: 87px;
    background: var(--accent);
    display: flex; align-items: center; justify-content: center;
  }
  .tagline {
    color: var(--paper); font-weight: 700; font-size: 17px;
    letter-spacing: 1.5px; text-transform: uppercase;
  }
  /* Front side */
  .card-front { left: 620px; background: var(--paper); }
  .card-front .brand {
    position: absolute; left: 30px; top: 84px; width: 170px;
    display: flex; align-items: center; gap: 10px;
  }
  .card-front .brand-name {
    color: var(--ink); font-weight: 800; font-size: 17px;
    letter-spacing: .5px; text-transform: uppercase; line-height: 1.15;
  }
  .divider {
    position: absolute; left: 212px; top: 52px; width: 1px; height: 150px;
    background: var(--rule);
  }
  .contact { position: absolute; left: 232px; right: 20px; top: 52px; }
  .person-name {
    font-weight: 800; font-size: 20px; color: var(--ink);
    text-transform: uppercase; line-height: 1.1;
  }
  .person-title { font-size: 15px; color: var(--accent); margin-bottom: 12px; }
  .contact-list { list-style: none; }
  .contact-list li {
    display: flex; align-items: center; gap: 8px; white-space: nowrap;
    font-size: 11.5px; color: var(--ink); line-height: 1.9;
  }
  .contact-list svg { width: 14px; height: 14px; flex: none; }
  .web-band {
    position: absolute; left: 0; right: 0; bottom: 0; height: 70px;
    background: var(--ink); border-top: 3px solid var(--accent);
    display: flex; align-items: center; justify-content: center;
  }
  .web-url { color: var(--accent); font-size: 16px; letter-spacing: 1.5px; }
</style>
</head>
<body>
  <section class="card card-back">
    <div class="brand">
      <span class="brand-mark"></span>
      <span class="brand-name">Coastline Premier<br>Retreats</span>
    </div>
    <div class="tagline-band">
      <p class="tagline">Luxury Hotel &amp; Resort Email Marketing</p>
    </div>
  </section>

  <section class="card card-front">
    <div class="brand">
      <span class="brand-mark"></span>
      <span class="brand-name">Coastline<br>Premier<br>Retreats</span>
    </div>
    <div class="divider"></div>
    <div class="contact">
      <p class="person-name">Daniel Hartley</p>
      <p class="person-title">Managing Director</p>
      <ul class="contact-list">
        <li>
          <svg viewBox="0 0 24 24"><path fill="var(--accent)" d="M6.6 10.8a15 15 0 0 0 6.6 6.6l2.2-2.2a1 1 0 0 1 1-.25 11.4 11.4 0 0 0 3.6.57 1 1 0 0 1 1 1V20a1 1 0 0 1-1 1A17 17 0 0 1 3 4a1 1 0 0 1 1-1h3.5a1 1 0 0 1 1 1c0 1.25.2 2.450.57 3.57a1 1 0 0 1-.25 1z"/></svg>
          044-555 210 347
        </li>
        <li>
          <svg viewBox="0 0 24 24"><rect x="6" y="2" width="12" height="20" rx="2" fill="none" stroke="var(--accent)" stroke-width="2"/><circle cx="12" cy="18" r="1.2" fill="var(--accent)"/></svg>
          044-555 210 348
        </li>
        <li>
          <svg viewBox="0 0 24 24"><rect x="2" y="5" width="20" height="14" fill="var(--accent)"/><path d="M2 5l10 8 10-8" fill="none" stroke="var(--paper)" stroke-width="1.6"/></svg>
          info@coastlinepremierretreats.example
        </li>
      </ul>
    </div>
    <div class="web-band">
      <p class="web-url">www.coastlinepremierretreats.example</p>
    </div>
  </section>
</body>
</html>
```